Business Card Design for company

We want new business cards. We'd like something different-- yet still highly professional. Our tagline is Providing leadership, delivering success. Stock photos are ok, as long as they are relevant and look upscale.

Target Market(s)

Architecture/Business Management Consulting/Engineering Consulting

Contact Information for Business Card

dark gray background with pops of blue might be good, but you tell me. You're the designers. Rounded corners might be nice, but again, you tell me.

Font styles to use
Serif
Sans Serif

Colors
3276b5
5c5c5c
9d9d9d
fbfbfb

Requirements
Nice to have
• Something different, but still very professional.

```html
<!DOCTYPE html>
<html lang="en">
<head>
<meta charset="utf-8">
<title>Norvale Advisory Business Cards</title>
<link rel="stylesheet" href="https://fonts.googleapis.com/css2?family=Open+Sans:wght@400;600;700&display=swap">
<style>
  :root {
    --blue: #3276b5;
    --blue-deep: #2a5f93;
    --charcoal: #5c5c5c;
    --graphite: #4a4d52;
    --slate: #9d9d9d;
    --paper: #fbfbfb;
    --backdrop: #1f1f20;
  }
  * { margin: 0; padding: 0; box-sizing: border-box; }
  html, body { width: 1200px; height: 885px; overflow: hidden; }
  body {
    background: var(--backdrop);
    font-family: "Open Sans", Arial, sans-serif;
    position: relative;
  }
  .card {
    position: absolute;
    width: 600px;
    height: 343px;
    border-radius: 6px;
    overflow: hidden;
    box-shadow: 0 18px 40px rgba(0,0,0,0.55);
  }
  /* Front */
  .card-front {
    left: 70px; top: 70px;
    background: linear-gradient(160deg, #8a9099 0%, #5f646b 45%, var(--graphite) 100%);
    display: flex; flex-direction: column; align-items: center; justify-content: center;
  }
  .brand-mark {
    display: flex; align-items: center; gap: 14px;
  }
  .brand-square {
    width: 26px; height: 26px; background: var(--blue);
  }
  .brand-name {
    font-weight: 700; font-size: 50px; letter-spacing: 6px; color: var(--paper);
  }
  .tagline {
    margin-top: 60px; font-size: 15px; color: var(--paper); letter-spacing: 0.3px;
  }
  .tagline .dot {
    display: inline-block; width: 6px; height: 6px; border-radius: 50%;
    background: var(--paper); margin: 0 8px; vertical-align: middle;
  }
  /* Back */
  .card-back {
    left: 530px; top: 472px;
    background: var(--paper);
  }
  .card-back .corners { position: absolute; inset: 0; }
  .holder {
    position: absolute; right: 60px; top: 40px; text-align: right;
  }
  .holder-name { font-weight: 700; font-size: 19px; color: var(--blue-deep); letter-spacing: 0.5px; }
  .holder-title { font-size: 12px; color: var(--charcoal); letter-spacing: 0.5px; }
  .company {
    position: absolute; left: 90px; top: 70px;
    font-weight: 700; font-size: 38px; line-height: 1.05; letter-spacing: 3px;
    color: var(--blue-deep);
  }
  .contact {
    position: absolute; left: 60px; bottom: 34px; right: 30px;
    font-size: 13px; color: var(--charcoal);
  }
  .address { margin-bottom: 8px; }
  .contact-grid { display: flex; gap: 36px; }
  .contact-list li { list-style: none; display: flex; align-items: center; gap: 8px; line-height: 1.6; }
  .contact-list svg { width: 13px; height: 13px; fill: var(--blue-deep); flex: none; }
</style>
</head>
<body>

<section class="card card-front" aria-label="Card front">
  <div class="brand-mark">
    <span class="brand-square"></span>
    <span class="brand-name">NORVALE</span>
  </div>
  <p class="tagline">Providing leadership<span class="dot"></span>delivering success</p>
</section>

<section class="card card-back" aria-label="Card back">
  <svg class="corners" viewBox="0 0 600 343" preserveAspectRatio="none" aria-hidden="true">
    <polygon points="0,0 110,0 0,110" fill="var(--blue-deep)"/>
    <polygon points="600,70 600,230 552,230" fill="var(--charcoal)"/>
  </svg>

  <div class="holder">
    <p class="holder-name">MARCUS HALE</p>
    <p class="holder-title">PRESIDENT</p>
  </div>

  <p class="company">NORVALE<br>ADVISORY</p>

  <div class="contact">
    <p class="address">2170 Harborline Avenue Lakewood, NY 11450</p>
    <div class="contact-grid">
      <ul class="contact-list">
        <li><svg viewBox="0 0 16 16"><path d="M3 1h3l1.5 4-2 1.3a9 9 0 0 0 4.2 4.2L11 8.5l4 1.5v3a2 2 0 0 1-2 2A12 12 0 0 1 1 3a2 2 0 0 1 2-2z"/></svg>555 0142 2207</li>
        <li><svg viewBox="0 0 16 16"><path d="M4 0h8a1 1 0 0 1 1 1v14a1 1 0 0 1-1 1H4a1 1 0 0 1-1-1V1a1 1 0 0 1 1-1zm1 2v10h6V2zm3 11a1 1 0 1 0 0 2 1 1 0 0 0 0-2z"/></svg>555 0178 3391</li>
      </ul>
      <ul class="contact-list">
        <li><svg viewBox="0 0 16 16"><path d="M1 3h14v10H1zm1.5 1.3V5l5.5 4 5.5-4v-.7z"/></svg>marcus@norvaleadvisory.com</li>
        <li><svg viewBox="0 0 16 16"><circle cx="8" cy="8" r="7"/></svg>www.norvaleadvisory.com</li>
      </ul>
    </div>
  </div>
</section>

</body>
</html>
```